Designer Instructions – Updated Referral Program Flyer

(Based on the mock-up in “Brief Layout and Instructions.pdf”)

OVERALL STYLE + LAYOUT

Maintain the same general layout, structure, and flow as the mock-up flyer (front and back).

This is an update of an older flyer, not a full redesign — keep the same sections, proportions, and overall visual feel, but with cleaner, more modern design improvements.

The final flyer should look clean, bold, professional, and high-impact, geared toward realtors, property managers, and contractors who refer work.

FRONT SIDE INSTRUCTIONS
1. Header Section

Remove the Rebuild Harbor Crest logo from the top banner.
(Shown on page 1 of the PDF)

2. Main Headline

Keep the same three-line structure:
EARN
UNLIMITED
CASH

Center it, maximize impact, and increase the font size of CASH so all three words match in importance.

Make the headline bold, clean, and the main focal point.

3. Cash Incentive Box

Keep the "$500 minimum OR 10% per referral" box, but upgrade the graphics to look sharper and more modern.

Ensure the wording matches exactly what’s in the mock-up.

4. Premier Partner Program Ribbon

Clean up and modernize the "PREMIER PARTNER PROGRAM" bar while keeping the same position and structure.

Ensure the checkmark badge remains crisp and professional.

5. Supporting Icons Section

Keep the four icons/benefit boxes (Guaranteed Payout, Free Evaluations, Affordable Solutions, Industry Leaders) in the same order.

Update the icons to cleaner, more modern styles — but maintain the same meanings.

Improve alignment and spacing for sharper visual consistency.

6. Remove Icons in Contact Area

At the bottom (“CALL TEXT OR BOOK ONLINE 858-471-6093 BrightlaneRenovate.com”), remove the phone and internet icons, as noted on page 2 of the PDF.

7. Replace All Images

I (Dorian) will provide all updated stock images separately via email.

Replace the flood/water-damage imagery and roof leak with the new images I send.

Keep image placement and proportions the same as the mock-up.

BACK SIDE INSTRUCTIONS
1. Header Image + “REFER / EARN” Section

Maintain the same large split-image layout (“The more you refer, the more you earn”).

Replace all background imagery with the new assets I will send.

Keep the CASH FLOW image section but modernize the type and spacing.

2. “HOW IT WORKS” Section

Preserve the three-column layout:

Refer Flood, Water & Mold Damage

We Take Care of Everything (evaluations/insurance)

Get Paid to Share

Update images, tighten spacing, and use modern iconography.

3. Remove Phone/Internet Icons

Same as the front side — remove small communication icons and keep only the text/number/URL.

4. Bottom Contact Bar

Keep the blue bar, same wording, same layout — just modernize the style if needed for clarity.

5. Replace All Back-Side Images

Again, I will email you the image assets.

Keep the layout EXACT — just update with higher-quality photos and improved design.

TEXT CONTENT (Keep as-is unless spacing adjustments needed)

All text shown in the PDF should remain exactly the same unless spacing or visual balance requires minor adjustments.
Example from page 3:

“REFER FLOOD, MOLD & CONSTRUCTION JOBS”

“We Schedule a Free Estimate. If Approved, You Get Paid.”

“Everybody Benefits From Referrals”

Everything stays, just refreshed and visually improved.

DESIGN GOALS

Flyer should look high-end and trustworthy, not salesy.

Consistent color theme: blues, whites, yellows, same palette as original.

Use bold, modern fonts with strong readability.

Ensure all headlines pop and all benefit boxes are clean, well-aligned, and evenly spaced.

The final result should feel like a premium referral program flyer for a top-tier restoration/remodel company.

FILES I WILL PROVIDE

I will send the designer:

All replacement stock photos

Any updated logos (if needed)

Original high-resolution version of the mock-up (if available)

Any additional icons preferred

Colors
0054AA
0677BA
7BADD7
CADEEF
E8F1F8

Requirements
Must have
• Designer Instructions – Updated Referral Program Flyer (Based on the mock-up in “Brief Layout and Instructions.pdf”) OVERALL STYLE + LAYOUT Maintain the same general layout, structure, and flow as the mock-up flyer (front and back). This is an update of an older flyer, not a full redesign — keep the same sections, proportions, and overall visual feel, but with cleaner, more modern design improvements. The final flyer should look clean, bold, professional, and high-impact, geared toward realtors, property managers, and contractors who refer work. FRONT SIDE INSTRUCTIONS 1. Header Section Remove the Rebuild Harbor Crest logo from the top banner. (Shown on page 1 of the PDF) 2. Main Headline Keep the same three-line structure: EARN UNLIMITED CASH Center it, maximize impact, and increase the font size of CASH so all three words match in importance. Make the headline bold, clean, and the main focal point. 3. Cash Incentive Box Keep the "$500 minimum OR 10% per referral" box, but upgrade the graphics to look sharper and more modern. Ensure the wording matches exactly what’s in the mock-up. 4. Premier Partner Program Ribbon Clean up and modernize the "PREMIER PARTNER PROGRAM" bar while keeping the same position and structure. Ensure the checkmark badge remains crisp and professional. 5. Supporting Icons Section Keep the four icons/benefit boxes (Guaranteed Payout, Free Evaluations, Affordable Solutions, Industry Leaders) in the same order. Update the icons to cleaner, more modern styles — but maintain the same meanings. Improve alignment and spacing for sharper visual consistency. 6. Remove Icons in Contact Area At the bottom (“CALL TEXT OR BOOK ONLINE 858-471-6093 BrightlaneRenovate.com”), remove the phone and internet icons, as noted on page 2 of the PDF. 7. Replace All Images I (Dorian) will provide all updated stock images separately via email. Replace the flood/water-damage imagery and roof leak with the new images I send. Keep image placement and proportions the same as the mock-up. BACK SIDE INSTRUCTIONS 1. Header Image + “REFER / EARN” Section Maintain the same large split-image layout (“The more you refer, the more you earn”). Replace all background imagery with the new assets I will send. Keep the CASH FLOW image section but modernize the type and spacing. 2. “HOW IT WORKS” Section Preserve the three-column layout: Refer Flood, Water & Mold Damage We Take Care of Everything (evaluations/insurance) Get Paid to Share Update images, tighten spacing, and use modern iconography. 3. Remove Phone/Internet Icons Same as the front side — remove small communication icons and keep only the text/number/URL. 4. Bottom Contact Bar Keep the blue bar, same wording, same layout — just modernize the style if needed for clarity. 5. Replace All Back-Side Images Again, I will email you the image assets. Keep the layout EXACT — just update with higher-quality photos and improved design. TEXT CONTENT (Keep as-is unless spacing adjustments needed) All text shown in the PDF should remain exactly the same unless spacing or visual balance requires minor adjustments. Example from page 3: “REFER FLOOD, MOLD & CONSTRUCTION JOBS” “We Schedule a Free Estimate. If Approved, You Get Paid.” “Everybody Benefits From Referrals” Everything stays, just refreshed and visually improved. DESIGN GOALS Flyer should look high-end and trustworthy, not salesy. Consistent color theme: blues, whites, yellows, same palette as original. Use bold, modern fonts with strong readability. Ensure all headlines pop and all benefit boxes are clean, well-aligned, and evenly spaced. The final result should feel like a premium referral program flyer for a top-tier restoration/remodel company. FILES I WILL PROVIDE I will send the designer: All replacement stock photos Any updated logos (if needed) Original high-resolution version of the mock-up (if available) Any additional icons preferred

```html
<!DOCTYPE html>
<html lang="en">
<head>
<meta charset="utf-8">
<title>Referral Program Flyer</title>
<link href="https://fonts.googleapis.com/css2?family=Cinzel:wght@700;900&family=Oswald:wght@500;600;700&family=Montserrat:wght@500;600;700;800&display=swap" rel="stylesheet">
<style>
  :root{
    --navy:#0b2a5b;
    --blue:#0054AA;
    --blue-mid:#0677BA;
    --blue-soft:#7BADD7;
    --blue-pale:#CADEEF;
    --blue-mist:#E8F1F8;
    --yellow:#f6c21c;
    --red:#d3262e;
    --slate:#5b6b7f;
    --white:#ffffff;
    --page:#e6e9ed;
  }
  *{box-sizing:border-box;margin:0;padding:0}
  html,body{width:880px;height:1200px;overflow:hidden}
  body{background:var(--page);font-family:'Montserrat',Arial,sans-serif;color:var(--navy);position:relative}

  .flyer{position:absolute;left:60px;width:760px;height:545px;background:var(--white);overflow:hidden;box-shadow:0 4px 14px rgba(0,0,0,.18)}
  .flyer--front{top:36px}
  .flyer--back{top:620px}

  /* ---------- FRONT ---------- */
  .hero-photo{position:absolute;top:0;right:0;width:470px;height:300px;
    background:linear-gradient(160deg,#b9c7d3 0%,#8da2b5 40%,#5f7b62 78%,#4a6a4f 100%)}
  .hero-panel{position:absolute;inset:0 0 auto 0;height:300px;background:linear-gradient(180deg,var(--navy),#0d3772);
    clip-path:polygon(0 0,56% 0,46% 100%,0 100%)}
  .hero-accent{position:absolute;inset:0 0 auto 0;height:300px;background:var(--blue-mid);
    clip-path:polygon(56% 0,57.4% 0,47.4% 100%,46% 100%)}
  .headline{position:absolute;top:46px;left:10px;width:360px;text-align:center;
    font-family:'Cinzel',Georgia,serif;font-weight:900;color:var(--white);line-height:1;text-transform:uppercase}
  .headline span{display:block}
  .headline .w-earn{font-size:58px}
  .headline .w-unlimited{font-size:42px;margin-top:4px}
  .headline .w-cash{font-size:66px;color:var(--yellow);margin-top:4px}
  .tagline{position:absolute;top:250px;left:0;width:330px;height:34px;background:var(--yellow);
    clip-path:polygon(0 0,100% 0,95% 100%,0 100%);
    font-family:'Oswald',Impact,sans-serif;font-weight:600;font-size:19px;letter-spacing:.04em;color:var(--navy);
    display:flex;align-items:center;padding-left:34px}

  .offer{position:absolute;top:318px;left:34px;display:flex;align-items:center}
  .offer-pill{background:var(--red);color:var(--white);height:40px;display:flex;align-items:center;gap:6px;
    padding:0 18px;font-weight:600;font-size:11px}
  .offer-pill strong{font-family:'Oswald',Impact,sans-serif;font-size:24px;font-weight:700}
  .offer-pill--left{border-radius:20px 0 0 20px;padding-right:26px}
  .offer-pill--right{border-radius:0 20px 20px 0;padding-left:26px}
  .offer-or{width:46px;height:46px;border-radius:50%;background:var(--white);border:3px solid var(--red);
    margin:0 -12px;z-index:1;display:flex;align-items:center;justify-content:center;
    font-family:'Oswald',Impact,sans-serif;font-weight:700;font-size:15px;color:var(--navy)}

  .partner{position:absolute;top:314px;right:34px;display:flex;align-items:center}
  .partner-block{height:36px;display:flex;align-items:center;font-family:'Oswald',Impact,sans-serif;
    font-weight:600;font-size:17px;letter-spacing:.06em;color:var(--white);padding:0 22px}
  .partner-block--left{background:var(--red);clip-path:polygon(0 50%,12% 0,100% 0,100% 100%,12% 100%);padding-left:30px}
  .partner-block--right{background:var(--slate);clip-path:polygon(0 0,88% 0,100% 50%,88% 100%,0 100%);padding-right:30px}
  .partner-badge{position:relative;width:54px;height:54px;border-radius:50%;background:var(--white);
    border:3px solid var(--navy);margin:0 -8px;z-index:1;display:flex;align-items:center;justify-content:center}
  .partner-tag{position:absolute;top:-16px;left:50%;transform:translateX(-50%);background:var(--red);color:var(--white);
    font-size:8px;font-weight:800;letter-spacing:.1em;padding:2px 6px}

  .wins{position:absolute;top:384px;left:0;width:100%;text-align:center;font-family:'Cinzel',Georgia,serif;
    font-weight:900;font-size:22px;color:var(--navy)}

  .benefits{position:absolute;top:426px;left:26px;right:26px;display:grid;grid-template-columns:repeat(4,1fr);gap:12px}
  .benefit{display:flex;gap:9px;align-items:flex-start}
  .benefit-icon{flex:0 0 42px;height:46px}
  .benefit h3{font-family:'Cinzel',Georgia,serif;font-weight:900;font-size:11px;line-height:1.2;color:var(--navy);text-transform:uppercase}
  .benefit p{font-size:9px;line-height:1.3;color:#4a5668;margin-top:3px}

  .contact-bar{position:absolute;bottom:0;left:0;width:100%;height:46px;background:var(--navy);
    display:flex;align-items:center;padding:0 30px;color:var(--white)}
  .contact-bar .cta{font-family:'Cinzel',Georgia,serif;font-weight:900;font-size:18px;flex:1}
  .contact-bar .phone{font-weight:700;font-size:14px;padding-right:18px;border-right:1px solid var(--blue-soft)}
  .contact-bar .web{font-weight:600;font-size:14px;padding-left:18px}
  .contact-bar::before{content:"";position:absolute;top:0;left:0;width:100%;height:4px;background:var(--yellow)}

  /* ---------- BACK ---------- */
  .money-photo{position:absolute;top:0;right:0;width:470px;height:290px;
    background:linear-gradient(135deg,#c9d3c2 0%,#9fb196 45%,#6f8a6d 100%)}
  .refer-panel{position:absolute;inset:0 0 auto 0;height:290px;background:linear-gradient(180deg,var(--blue),var(--navy));
    clip-path:polygon(0 0,52% 0,42% 100%,0 100%)}
  .refer-accent{position:absolute;inset:0 0 auto 0;height:290px;background:var(--yellow);
    clip-path:polygon(52% 0,53.2% 0,43.2% 100%,42% 100%)}
  .refer-copy{position:absolute;top:20px;left:34px;font-family:'Oswald',Impact,sans-serif;font-weight:700;
    text-transform:uppercase;line-height:1;color:var(--white)}
  .refer-copy span{display:block}
  .refer-copy .small{font-size:28px}
  .refer-copy .big{font-size:62px;color:var(--yellow)}
  .how{position:absolute;top:268px;left:0;width:300px;height:42px;background:var(--yellow);
    clip-path:polygon(0 0,100% 0,93% 100%,0 100%);display:flex;align-items:center;padding-left:34px;
    font-family:'Cinzel',Georgia,serif;font-weight:900;font-size:22px;color:var(--navy)}

  .steps{position:absolute;top:324px;left:26px;right:26px;display:grid;grid-template-columns:repeat(3,1fr);gap:16px}
  .step{background:var(--blue-mist);border:1px solid var(--blue-pale);height:160px}
  .step-photo{height:70px}
  .step-photo--flood{background:linear-gradient(160deg,#a6b6c4,#6f8799)}
  .step-photo--team{background:linear-gradient(160deg,#d2c7b5,#9a8b74)}
  .step-photo--share{background:linear-gradient(160deg,#9fc0dd,#f0cf4a)}
  .step h3{background:var(--navy);color:var(--white);font-family:'Cinzel',Georgia,serif;font-weight:900;
    font-size:11px;line-height:1.25;text-transform:uppercase;padding:7px 10px;min-height:44px;display:flex;align-items:center}
  .step p{font-size:10px;line-height:1.35;color:#34425a;padding:7px 10px}
</style>
</head>
<body>

<section class="flyer flyer--front">
  <div class="hero-photo" role="img" aria-label="Photo of a homeowner holding an insurance claim clipboard in front of a house"></div>
  <div class="hero-panel"></div>
  <div class="hero-accent"></div>

  <h1 class="headline">
    <span class="w-earn">Earn</span>
    <span class="w-unlimited">Unlimited</span>
    <span class="w-cash">Cash</span>
  </h1>
  <div class="tagline">GET PAID TO REFER A FLOOD</div>

  <div class="offer">
    <div class="offer-pill offer-pill--left"><strong>$500</strong>minimum</div>
    <div class="offer-or">OR</div>
    <div class="offer-pill offer-pill--right"><strong>10%</strong>per referral</div>
  </div>

  <div class="partner">
    <div class="partner-block partner-block--left">PARTNER</div>
    <div class="partner-badge">
      <span class="partner-tag">PREMIER</span>
      <svg width="26" height="26" viewBox="0 0 26 26"><path d="M5 13.5l5 5L21 7.5" fill="none" stroke="#d3262e" stroke-width="4" stroke-linecap="round" stroke-linejoin="round"/></svg>
    </div>
    <div class="partner-block partner-block--right">PROGRAM</div>
  </div>

  <h2 class="wins">PARTNER WITH US &amp; EVERYBODY WINS!</h2>

  <div class="benefits">
    <div class="benefit">
      <svg class="benefit-icon" viewBox="0 0 42 46"><polygon points="21,1 41,12 41,34 21,45 1,34 1,12" fill="#0b2a5b"/><text x="21" y="30" text-anchor="middle" font-family="Oswald, sans-serif" font-weight="700" font-size="20" fill="#f6c21c">$</text></svg>
      <div><h3>Guaranteed<br>Payout</h3><p>Fast payment on every approved job</p></div>
    </div>
    <div class="benefit">
      <svg class="benefit-icon" viewBox="0 0 42 46"><polygon points="21,1 41,12 41,34 21,45 1,34 1,12" fill="#0b2a5b"/><rect x="13" y="13" width="16" height="20" rx="2" fill="none" stroke="#f6c21c" stroke-width="2"/><path d="M16 23l3 3 6-6" fill="none" stroke="#f6c21c" stroke-width="2" stroke-linecap="round"/></svg>
      <div><h3>Free<br>Estimates</h3><p>No-cost inspection for every referral</p></div>
    </div>
    <div class="benefit">
      <svg class="benefit-icon" viewBox="0 0 42 46"><polygon points="21,1 41,12 41,34 21,45 1,34 1,12" fill="#0b2a5b"/><path d="M12 14h10l9 9-9 9-10-10z" fill="none" stroke="#f6c21c" stroke-width="2" stroke-linejoin="round"/><circle cx="16.5" cy="18.5" r="2" fill="#f6c21c"/></svg>
      <div><h3>Affordable<br>Solutions</h3><p>Fair pricing with insurance support</p></div>
    </div>
    <div class="benefit">
      <svg class="benefit-icon" viewBox="0 0 42 46"><polygon points="21,1 41,12 41,34 21,45 1,34 1,12" fill="#0b2a5b"/><polygon points="21,12 24,19.5 32,20 26,25 28,33 21,28.5 14,33 16,25 10,20 18,19.5" fill="#f6c21c"/></svg>
      <div><h3>Industry<br>Leaders</h3><p>Trusted experts in restoration work</p></div>
    </div>
  </div>

  <footer class="contact-bar">
    <span class="cta">CALL, TEXT OR BOOK ONLINE</span>
    <span class="phone">858-471-6093</span>
    <span class="web">www.BrightlaneRenovate.com</span>
  </footer>
</section>

<section class="flyer flyer--back">
  <div class="money-photo" role="img" aria-label="Photo of scattered hundred-dollar bills with letter tiles spelling cash flow"></div>
  <div class="refer-panel"></div>
  <div class="refer-accent"></div>

  <h1 class="refer-copy">
    <span class="small">The more you</span>
    <span class="big">Refer</span>
    <span class="small">The more you</span>
    <span class="big">Earn</span>
  </h1>

  <h2 class="how">HOW IT WORKS</h2>

  <div class="steps">
    <article class="step">
      <div class="step-photo step-photo--flood" role="img" aria-label="Photo of a flooded room with water damage"></div>
      <h3>Refer Flood, Mold &amp; Construction Jobs</h3>
      <p>It's Simple to Refer. Call, Text or Book Online.</p>
    </article>
    <article class="step">
      <div class="step-photo step-photo--team" role="img" aria-label="Photo of a restoration crew at work"></div>
      <h3>We Take Care of Everything</h3>
      <p>We Schedule a Free Estimate. If Approved, You Get Paid.</p>
    </article>
    <article class="step">
      <div class="step-photo step-photo--share" role="img" aria-label="Photo of a yellow road sign reading get paid to share"></div>
      <h3>Everybody Benefits From Referrals</h3>
      <p>We Provide Expert Quality Work for Affordable Prices.</p>
    </article>
  </div>

  <footer class="contact-bar">
    <span class="cta">CALL, TEXT OR BOOK ONLINE</span>
    <span class="phone">858-471-6093</span>
    <span class="web">www.BrightlaneRenovate.com</span>
  </footer>
</section>

</body>
</html>
```